Business Cards used to invite people to our church

We are a church and have need of a business card sized advertisement that allows our members to hand them out in order to invite people to the church. I need the front of the card to say "You're Invited" or "Come Check us out". with the service times on the back of the card later.
I have attached one of the OLD cards we have used in the past, but we want a complete makeover, into a more modern style that does not require the image.
I am also replacing the old logo with a newer "flat" logo which is attached.
Please use marketing colors. (blue or red or something that catches attention)
Create a card that DOES NOT have the picture of the two people on the front
The information on the sample card back is correct to go onto new card
Target Market(s)
anyone
Industry/Entity Type
Business
Contact Information for Business Card
sertice times and address information which you can get from the sample card I uploaded. It should have "You're Invited" or "Come Check us out" on the front of the card with out logo.

```html
<!DOCTYPE html>
<html lang="en">
<head>
<meta charset="utf-8">
<title>Grace Harbor – Invitation Cards</title>
<link rel="stylesheet" href="https://fonts.googleapis.com/css2?family=Open+Sans:wght@400;600&display=swap">
<style>
  :root {
    --page: #e9e6e1;
    --ink-red: #ee2a3a;
    --ink-white: #ffffff;
    --sky-light: #dfe9f3;
    --sky-blue: #6f93bd;
    --sky-deep: #2c3550;
    --night: #0a0a0d;
    --card-shadow: rgba(0, 0, 0, 0.28);
  }
  * { box-sizing: border-box; margin: 0; padding: 0; }
  html, body {
    width: 1200px; height: 913px; overflow: hidden;
    background: var(--page);
    font-family: "Open Sans", Arial, sans-serif;
  }
  .sheet {
    position: relative; width: 1200px; height: 913px;
    display: flex; justify-content: center; align-items: center; gap: 54px;
  }
  .card {
    position: relative; width: 520px; height: 297px;
    overflow: hidden; border-radius: 3px;
    box-shadow: 0 14px 30px var(--card-shadow);
    background: var(--night);
  }
  .card__sky {
    position: absolute; inset: 0;
    background:
      radial-gradient(ellipse 60% 55% at 62% 0%, var(--sky-light) 0%, rgba(223,233,243,0.55) 30%, transparent 65%),
      linear-gradient(115deg, var(--sky-blue) 0%, var(--sky-deep) 40%, var(--night) 68%, var(--night) 100%);
  }
  /* front */
  .front__headline {
    position: absolute; left: 34px; top: 150px;
    color: var(--ink-red); font-weight: 400; font-size: 40px; letter-spacing: 3px;
    text-transform: uppercase;
  }
  .front__brand {
    position: absolute; right: 30px; top: 40px;
    display: flex; align-items: center; gap: 10px;
    color: var(--ink-red); font-weight: 600; font-size: 24px;
  }
  .front__brand-dot {
    width: 16px; height: 16px; border-radius: 50%; background: var(--ink-red);
  }
  /* back */
  .back__contact {
    position: absolute; left: 34px; top: 28px;
    color: var(--ink-red); font-size: 14px; font-weight: 600; line-height: 1.45;
    text-transform: uppercase;
  }
  .back__times {
    position: absolute; left: 34px; right: 34px; bottom: 30px;
    list-style: none; color: var(--ink-white); font-size: 14px; text-transform: uppercase;
  }
  .back__times li {
    display: flex; align-items: baseline; gap: 6px; margin-top: 10px;
  }
  .back__times .leader {
    flex: 1; border-bottom: 2px dotted var(--ink-white); transform: translateY(-3px);
  }
</style>
</head>
<body>
<main class="sheet">
  <section class="card card--front">
    <div class="card__sky" role="img" aria-label="Sky photo with light rays breaking through clouds"></div>
    <div class="front__brand"><span class="front__brand-dot"></span>Grace Harbor</div>
    <h1 class="front__headline">You're Invited</h1>
  </section>

  <section class="card card--back">
    <div class="card__sky" role="img" aria-label="Sky photo with light rays breaking through clouds"></div>
    <address class="back__contact">
      P: 1-800-555-0142<br>
      www.graceharbor.org<br>
      A: 420 Elm Creek Road - Fairview, TX 75000
    </address>
    <ul class="back__times">
      <li><span>Sunday</span><span class="leader"></span><span>9:00 AM</span></li>
      <li><span>Sunday</span><span class="leader"></span><span>11:00 AM</span></li>
      <li><span>Wed. Bible Class</span><span class="leader"></span><span>7:00 PM</span></li>
    </ul>
  </section>
</main>
</body>
</html>
```